Harborline Claims Advocates Business card

We need to get business card Design for our Company we are Public Adjusters in Chicago Illinois - i like to see good combination and elements from my Company Logo. as well To be an two side design
Updates

Target Market(s)

Home /Business owner Property Managers

Industry/Entity Type

Business

Contact Information for Business Card

to show the Element of our logo i will Like 3D

Font styles to use
Sans Serif

Requirements
Must have
• Logo and Element of the Logo in 3D
Nice to have
• Logo That we Provide 3D Same Colors or open for suggestions
Should not have
• unleare view -

```html
<!DOCTYPE html>
<html lang="en">
<head>
<meta charset="utf-8">
<title>Harborline Claims Advocates – Business Card</title>
<link rel="stylesheet" href="https://fonts.googleapis.com/css2?family=Oswald:wght@500;600&family=Open+Sans:wght@400;600;700&display=swap">
<style>
  :root {
    --navy-deep: #0d1656;
    --navy: #1a2a8c;
    --royal: #2246c9;
    --orange: #e0643a;
    --white: #ffffff;
    --brand-blue: #2f5fd0;
    --stage: #e9e6e1;
    --text-light: #e8ecff;
  }
  * { box-sizing: border-box; margin: 0; padding: 0; }
  html, body {
    width: 1200px; height: 795px; overflow: hidden;
    background: var(--stage);
    font-family: "Open Sans", Arial, sans-serif;
  }
  .sheet {
    position: relative; width: 1200px; height: 795px;
    display: flex; align-items: center; justify-content: center; gap: 40px;
  }
  .card {
    position: relative; width: 540px; height: 310px; overflow: hidden;
    border-radius: 4px;
    box-shadow: 0 10px 24px rgba(0,0,0,.22);
  }

  /* Front side */
  .card--front {
    background: radial-gradient(ellipse at 65% 40%, var(--royal) 0%, var(--navy) 45%, var(--navy-deep) 100%);
  }
  .front-shape { position: absolute; inset: 0; width: 100%; height: 100%; }
  .brand-block {
    position: absolute; left: 14px; top: 0; width: 200px; height: 310px;
    display: flex; flex-direction: column; align-items: center; justify-content: center; gap: 10px;
    text-align: center;
  }
  .brand-mark {
    width: 34px; height: 34px; border-radius: 50%;
    background: var(--brand-blue);
  }
  .brand-name {
    color: var(--brand-blue); font-weight: 700; font-size: 15px; line-height: 1.25;
  }
  .details {
    position: absolute; left: 290px; top: 34px; right: 20px;
    color: var(--text-light);
  }
  .person-name {
    font-family: "Oswald", Arial, sans-serif; font-weight: 600;
    font-size: 28px; letter-spacing: 1.5px; color: var(--white); line-height: 1.1;
  }
  .person-title { font-size: 13px; margin-top: 2px; opacity: .9; }
  .address { font-size: 12.5px; line-height: 1.45; margin-top: 22px; }
  .contact-list { list-style: none; margin-top: 16px; font-size: 12.5px; }
  .contact-list li {
    display: flex; align-items: center; gap: 9px; line-height: 1.6;
  }
  .contact-list svg { width: 12px; height: 12px; flex: none; fill: var(--white); }

  /* Back side */
  .card--back {
    background: radial-gradient(ellipse at 50% 45%, var(--royal) 0%, var(--navy) 50%, var(--navy-deep) 100%);
    display: flex; flex-direction: column; align-items: center; justify-content: center;
  }
  .back-line { position: absolute; inset: 0; width: 100%; height: 100%; }
  .back-brand {
    position: relative; display: flex; align-items: center; gap: 12px;
  }
  .back-brand .brand-mark { width: 40px; height: 40px; background: var(--orange); }
  .back-brand .brand-name { color: var(--white); font-size: 20px; text-align: left; }
  .web-address {
    position: relative; margin-top: 28px;
    font-size: 12px; letter-spacing: 2.5px; color: var(--text-light); opacity: .85;
  }
</style>
</head>
<body>
<main class="sheet">

  <section class="card card--front" aria-label="Business card front">
    <svg class="front-shape" viewBox="0 0 540 310" aria-hidden="true">
      <path d="M168 0 C282 80 276 230 208 310 H190 C252 230 262 80 150 0 Z" fill="var(--orange)"/>
      <path d="M0 0 H150 C262 80 252 230 190 310 H0 Z" fill="var(--white)"/>
    </svg>

    <div class="brand-block">
      <span class="brand-mark" aria-hidden="true"></span>
      <p class="brand-name">Harborline Claims<br>Advocates</p>
    </div>

    <div class="details">
      <h1 class="person-name">EVAN HALE</h1>
      <p class="person-title">CEO/Founder</p>
      <p class="address">4120 Linden Court<br>Evanston, Illinois 60201</p>
      <ul class="contact-list">
        <li><svg viewBox="0 0 12 12"><path d="M2.5 1 L4.5 1 L5.3 3.4 L4 4.4 C4.6 5.8 6 7.3 7.6 8 L8.6 6.7 L11 7.5 L11 9.5 C11 10.4 10.3 11 9.4 11 C5 10.6 1.4 7 1 2.6 C1 1.7 1.6 1 2.5 1 Z"/></svg>312 555 0148</li>
        <li><svg viewBox="0 0 12 12"><path d="M3 0.5 H9 V11.5 H3 Z M4 1.5 V9.5 H8 V1.5 Z" fill-rule="evenodd"/></svg>312 555 0193</li>
        <li><svg viewBox="0 0 12 12"><path d="M1 4 H11 V10 H1 Z M3 1 H9 V4 H3 Z"/></svg>312 555 0172</li>
        <li><svg viewBox="0 0 12 12"><path d="M1 2.5 H11 V9.5 H1 Z M1.8 3.2 L6 6.4 L10.2 3.2 Z" fill-rule="evenodd"/></svg>hello@harborlineclaims.com</li>
        <li><svg viewBox="0 0 12 12"><circle cx="6" cy="6" r="5"/></svg>www.harborlineclaims.com</li>
      </ul>
    </div>
  </section>

  <section class="card card--back" aria-label="Business card back">
    <svg class="back-line" viewBox="0 0 540 310" aria-hidden="true">
      <line x1="40" y1="250" x2="500" y2="250" stroke="rgba(255,255,255,.35)" stroke-width="1"/>
    </svg>
    <div class="back-brand">
      <span class="brand-mark" aria-hidden="true"></span>
      <p class="brand-name">Harborline Claims<br>Advocates</p>
    </div>
    <p class="web-address">HarborlineClaims.com</p>
  </section>

</main>
</body>
</html>
```